Banner Pop Up Opt In Form REDESIGNS - SLEEK BLACK LOOK

Please redesign banners attached.

I am looking for a very sleek look....I do not like this collage of images on these current designs. Please keep all content same but use images that pop.

I have an acccount at www.pixvane-example.com or you can use your own images.

I like black background for somereason because it looks very sleek....but these designs should pop , build trust and credibility and have easy opt in form....SLEEK AND MODERN LOOK is what im looking for....

Target Market(s)

Consumers on websites

Requirements
Must have
• Please redesign banners attached.

Nice to have

Should not have

```html
<!DOCTYPE html>
<html lang="en">
<head>
<meta charset="utf-8">
<title>Las Vegas Hotel &amp; Casino Opt-In Banners</title>
<link rel="stylesheet" href="https://fonts.googleapis.com/css2?family=Questrial&family=Abel&display=swap">
<style>
  :root {
    --bg-deep: #0b0b0b;
    --bg-soft: #262626;
    --gold-light: #fff2b0;
    --gold-mid: #d9ad3c;
    --gold-dark: #8a6418;
    --gold-text: #d8b45a;
    --red: #ff1a1a;
    --red-dark: #b80000;
    --white: #ffffff;
    --divider: #9a9a9a;
    --chip-red: #c9202a;
    --chip-white: #e9e9e9;
  }
  * { margin: 0; padding: 0; box-sizing: border-box; }
  html, body { width: 1200px; height: 516px; overflow: hidden; background: var(--bg-deep); }
  .canvas { position: relative; width: 1200px; height: 516px; display: flex; }
  .banner {
    position: relative; width: 600px; height: 516px; overflow: hidden;
    background: radial-gradient(ellipse at 55% 45%, var(--bg-soft) 0%, #151515 55%, var(--bg-deep) 100%);
  }
  .banner + .banner { border-left: 1px solid var(--divider); }
  .headline {
    position: absolute; left: 0; width: 600px; text-align: center;
    font-family: "Questrial", sans-serif; font-weight: 400; text-transform: uppercase;
    line-height: 1; letter-spacing: -3px; white-space: nowrap;
    background: linear-gradient(180deg, var(--gold-light) 0%, var(--gold-mid) 45%, var(--gold-dark) 70%, var(--gold-mid) 100%);
    -webkit-background-clip: text; background-clip: text; color: transparent;
  }
  .headline--stacked { top: 8px; font-size: 80px; }
  .headline--stacked span { display: block; height: 70px; }
  .headline--single { top: 23px; font-size: 80px; }
  .offer {
    position: absolute; left: 0; width: 600px; text-align: center;
    font-family: "Abel", sans-serif; text-transform: uppercase; line-height: 1;
    white-space: nowrap;
  }
  .offer__lead { font-size: 20.5px; color: var(--gold-text); }
  .offer__prize { font-size: 20.5px; color: var(--red); margin-top: 3px; }
  .optin-form { position: absolute; }
  .field {
    display: block; width: 268px; height: 42px; margin-bottom: 18px;
    background: var(--white);
    border: 3px solid var(--gold-mid);
    box-shadow: inset 0 0 0 1px var(--gold-light);
  }
  .submit {
    position: absolute; width: 114px; height: 32px;
    background: linear-gradient(180deg, var(--red) 0%, #f00 60%, var(--red-dark) 100%);
    border-radius: 2px;
    font-family: "Abel", sans-serif; font-size: 24px; color: #000; line-height: 32px;
    text-align: center;
  }
  .casino-art {
    position: absolute;
    background: radial-gradient(ellipse at 45% 40%, var(--chip-red) 0%, #5a1a1a 30%, #3a3a3a 55%, transparent 72%);
    opacity: 0.85;
  }
  .fine-print {
    position: absolute; bottom: 12px;
    font-family: "Questrial", sans-serif; font-size: 10.5px; color: var(--white);
    text-transform: uppercase; white-space: nowrap;
  }
</style>
</head>
<body>
<main class="canvas">
  <section class="banner banner--offer">
    <h1 class="headline headline--stacked"><span>Want a</span><span>Great Offer?</span></h1>
    <div class="offer" style="top:169px;">
      <p class="offer__lead">Subscribe to our newsletter and receive a complimentary</p>
      <p class="offer__prize">1-4 Night Las Vegas Hotel &amp; Casino</p>
    </div>
    <form class="optin-form" style="left:33px; top:243px;">
      <span class="field"></span>
      <span class="field"></span>
      <span class="field"></span>
    </form>
    <div class="submit" style="left:103px; top:422px;">SUBMIT</div>
    <div class="casino-art" role="img" aria-label="Stack of red, white and black casino chips with two white dice" style="left:324px; top:233px; width:242px; height:247px;"></div>
    <p class="fine-print" style="left:35px;">We will send an email and a text mesage with the offer and how to redeem</p>
  </section>

  <section class="banner banner--contest">
    <h1 class="headline headline--single">Enter to Win!</h1>
    <div class="offer" style="top:120px;">
      <p class="offer__lead">Subscribe to our newsletter and receive a complimentary</p>
      <p class="offer__prize">1-4 Night Las Vegas Hotel &amp; Casino</p>
    </div>
    <form class="optin-form" style="left:33px; top:224px;">
      <span class="field"></span>
      <span class="field"></span>
      <span class="field"></span>
    </form>
    <div class="submit" style="left:103px; top:402px;">SUBMIT</div>
    <div class="casino-art" role="img" aria-label="Stack of red, white and black casino chips with two white dice" style="left:324px; top:213px; width:240px; height:241px;"></div>
    <p class="fine-print" style="left:35px;">We will send an email and a text mesage with the offer and how to redeem</p>
  </section>
</main>
</body>
</html>
```